Business Card for a New Zealand IT Startup

I need a business card for VELTA Holdings. We are a young startup based in New Zealand working in internet marketing and web development. The design should have some element connected to New Zealand, such as wave, koru or silver fern, just don't use a kiwi bird.

```html
<!DOCTYPE html>
<html lang="en">
<head>
<meta charset="UTF-8">
<title>VELTA Holdings – Business Card</title>
<link href="https://fonts.googleapis.com/css2?family=Montserrat:wght@500;600;700&family=Open+Sans:wght@400;600&display=swap" rel="stylesheet">
<style>
  :root {
    --bg: #d9d9d9;
    --card: #f7f7f7;
    --blue: #0f6cb6;
    --orange: #ef5a24;
    --ink: #3a3a3a;
    --muted: #555555;
    --wave: #e6e6e6;
    --wave-soft: #eeeeee;
  }
  * { margin: 0; padding: 0; box-sizing: border-box; }
  html, body { width: 1200px; height: 852px; overflow: hidden; }
  body {
    background: var(--bg);
    font-family: "Open Sans", sans-serif;
    position: relative;
  }
  .card {
    position: absolute;
    top: 266px;
    width: 520px;
    height: 320px;
    background: var(--card);
    border-radius: 22px;
    box-shadow: 0 6px 18px rgba(0,0,0,0.18);
    overflow: hidden;
  }
  .card--front { left: 50px; }
  .card--back { left: 630px; }

  .wordmark {
    font-family: "Montserrat", sans-serif;
    font-weight: 700;
    color: var(--blue);
    letter-spacing: 1px;
    display: flex;
    align-items: center;
    gap: 12px;
    white-space: nowrap;
  }
  .wordmark__dot {
    width: 16px; height: 16px;
    background: var(--orange);
    border-radius: 50%;
    flex: none;
  }

  /* front */
  .card--front .wordmark {
    position: absolute;
    top: 112px; left: 0; right: 0;
    justify-content: center;
    font-size: 42px;
  }
  .front__web {
    position: absolute;
    top: 222px; left: 0; right: 0;
    display: flex; align-items: center; justify-content: center; gap: 14px;
    font-size: 13px; color: var(--ink);
  }
  .front__web .hl { color: var(--orange); }
  .front__rule { width: 70px; height: 2px; background: var(--blue); }

  /* back: Pacific wave bands */
  .back__waves {
    position: absolute;
    right: 0; bottom: 0;
    width: 300px; height: 260px;
  }
  .back__edge {
    position: absolute; left: 0; top: 120px;
    width: 6px; height: 46px;
    background: linear-gradient(var(--orange) 50%, var(--blue) 50%);
  }
  .card--back .wordmark {
    position: absolute;
    top: 40px; right: 34px;
    font-size: 26px;
  }
  .person {
    position: absolute; top: 104px; left: 38px;
  }
  .person__name {
    font-family: "Montserrat", sans-serif;
    font-weight: 700; font-size: 20px; color: var(--blue);
  }
  .person__role { font-size: 11px; color: var(--muted); margin-top: 2px; }

  .contacts {
    position: absolute; left: 38px; bottom: 34px;
    list-style: none;
    font-size: 13px; color: var(--ink);
  }
  .contacts li { display: flex; align-items: center; gap: 10px; line-height: 22px; }
  .contacts svg { width: 12px; height: 12px; fill: var(--orange); flex: none; }
  .contacts .address { margin-top: 4px; }
</style>
</head>
<body>

<section class="card card--front" aria-label="Card front">
  <div class="wordmark"><span class="wordmark__dot"></span>VELTA Holdings</div>
  <div class="front__web">
    <span class="front__rule"></span>
    <span>www.<span class="hl">velta</span>holdings.com</span>
    <span class="front__rule"></span>
  </div>
</section>

<section class="card card--back" aria-label="Card back">
  <svg class="back__waves" viewBox="0 0 300 260" aria-hidden="true">
    <path d="M0 150 C50 120 100 180 150 150 S250 120 300 150 V260 H0Z" fill="var(--wave-soft)"/>
    <path d="M0 185 C50 155 100 215 150 185 S250 155 300 185 V260 H0Z" fill="var(--wave)"/>
    <path d="M0 220 C50 190 100 250 150 220 S250 190 300 220 V260 H0Z" fill="#dedede"/>
  </svg>
  <div class="back__edge"></div>
  <div class="wordmark"><span class="wordmark__dot"></span>VELTA Holdings</div>

  <div class="person">
    <div class="person__name">Mara Quinn</div>
    <div class="person__role">Managing Director</div>
  </div>

  <ul class="contacts">
    <li>
      <svg viewBox="0 0 12 12"><path d="M2.5 1h2l1 2.5-1.3 1a6 6 0 0 0 3.3 3.3l1-1.3 2.5 1v2a1 1 0 0 1-1 1A9 9 0 0 1 1.5 2a1 1 0 0 1 1-1z"/></svg>
      888-5550-142
    </li>
    <li>
      <svg viewBox="0 0 12 12"><path d="M1 2.5h10v7H1z M1.6 3 6 6.4 10.4 3" fill="none" stroke="#ef5a24" stroke-width="1.2"/></svg>
      hello@veltaholdings.com
    </li>
    <li>
      <svg viewBox="0 0 12 12"><circle cx="6" cy="6" r="5"/><path d="M1 6h10M6 1c-2 2.6-2 7.4 0 10M6 1c2 2.6 2 7.4 0 10" stroke="#f7f7f7" stroke-width="0.9" fill="none"/></svg>
      www.veltaholdings.com
    </li>
    <li class="address">58 Harbour Lane, Te Aro, Wellington, NZ 6011</li>
  </ul>
</section>

</body>
</html>
```